Business card design needed

Business Card design required for new small plumbing business.
Would like a logo/text look that is simple and unique and does not have to be representative of a plumbing company (ie. having a cartoon plumber or toilet etc) as the companyname is self explanatory.
Would like the main colour to be green (lime green).

Industry/Entity Type

Plumber

Contact Information for Business Card

BRAMFORD PLUMBING
ABN 71 546 190 327 004

Simon Harcastle
Licensed Plumber 83615
Phone: 0487 214 670

27 Bramford Drive,
Harrowvale. 3927 Westmere

Email: bramfordplumbing@quellmail.example

Logo Text

Bramford Plumbing

Logo styles of interest
Character Logo
Wordmark Logo
Lettermark Logo

```html
<!DOCTYPE html>
<html lang="en">
<head>
<meta charset="utf-8">
<title>Bramford Plumbing – Business Card</title>
<link rel="stylesheet" href="https://fonts.googleapis.com/css2?family=Tinos&family=Cormorant+Garamond:wght@500&family=Questrial&display=swap">
<style>
  :root {
    --lime: #58ff00;
    --navy: #10166a;
    --paper: #ffffff;
    --smoke-strong: rgba(88, 255, 0, 0.38);
    --smoke-soft: rgba(88, 255, 0, 0.06);
  }
  html, body {
    margin: 0;
    padding: 0;
    width: 1200px;
    height: 741px;
    overflow: hidden;
    background: var(--paper);
  }
  .card {
    position: relative;
    width: 1200px;
    height: 741px;
    background: var(--paper);
    color: var(--navy);
    font-family: "Questrial", "Century Gothic", sans-serif;
  }
  .band {
    position: absolute;
    left: 0;
    width: 1200px;
    background: var(--lime);
  }
  .band--top { top: 0; height: 84px; }
  .band--bottom { bottom: 0; height: 86px; }
  .abn {
    position: absolute;
    right: 30px;
    top: 24px;
    margin: 0;
    font-family: "Tinos", "Times New Roman", serif;
    font-size: 30px;
    line-height: 1;
  }
  .email {
    position: absolute;
    right: 29px;
    bottom: 25px;
    margin: 0;
    font-size: 29px;
    line-height: 1;
    white-space: nowrap;
  }
  .smoke {
    position: absolute;
    left: 0;
    top: 84px;
    width: 300px;
    height: 571px;
    background:
      radial-gradient(ellipse 55% 35% at 40% 18%, var(--smoke-strong), transparent 70%),
      linear-gradient(90deg, var(--smoke-soft) 0%, var(--smoke-strong) 25%, var(--smoke-soft) 55%, transparent 100%);
  }
  .brand {
    position: absolute;
    left: 218px;
    top: 268px;
    width: 340px;
    margin: 0;
    font-size: 44px;
    line-height: 1.1;
    letter-spacing: 1px;
    text-align: center;
    color: var(--navy);
    font-weight: 400;
  }
  .brand__dot {
    display: block;
    width: 34px;
    height: 34px;
    margin: 0 auto 12px;
    border-radius: 50%;
    background: var(--lime);
  }
  .divider {
    position: absolute;
    left: 580px;
    top: 184px;
    width: 2px;
    height: 325px;
    background: var(--lime);
  }
  .contact {
    position: absolute;
    left: 614px;
    top: 252px;
  }
  .contact__name {
    margin: 0 0 18px;
    font-family: "Cormorant Garamond", "Palatino Linotype", serif;
    font-weight: 500;
    font-size: 54px;
    line-height: 1;
  }
  .contact__line {
    margin: 0;
    font-size: 29px;
    line-height: 41px;
    white-space: nowrap;
  }
</style>
</head>
<body>
  <main class="card">
    <header class="band band--top">
      <p class="abn">ABN 71 546 190 327 004</p>
    </header>

    <div class="smoke" role="img" aria-label="Soft lime green smoke wisp rising along the left edge"></div>

    <h1 class="brand"><span class="brand__dot"></span>BRAMFORD<br>PLUMBING</h1>

    <div class="divider"></div>

    <section class="contact">
      <h2 class="contact__name">Simon Harcastle</h2>
      <p class="contact__line">Licensed Plumber 83615</p>
      <p class="contact__line">Phone: 0487 214 670 27</p>
      <p class="contact__line">Bramford Drive, Harrowvale. 3927 Westmere</p>
    </section>

    <footer class="band band--bottom">
      <p class="email">Email: bramfordplumbing@quellmail.example</p>
    </footer>
  </main>
</body>
</html>
```